Bork Ventures, Inc. Website redesign

Revamp the website, it is old and outdated. www.borkventuresinc.example

Target Market(s)

Information Technology Consulting and Staffing

Coding

Coded - Design and coding required

Number of Pages Required

5+ page

Colors

Designer to choose colors to be used in the design.

Requirements
Must have
• Outlined text boxes just like from the Tolvane.example site. A clean look

```html
<!DOCTYPE html>
<html lang="en">
<head>
<meta charset="utf-8">
<title>Bork Ventures, Inc. | IT Consulting</title>
<link rel="stylesheet" href="https://fonts.googleapis.com/css2?family=Poppins:wght@500;600;700;800&family=Overpass:wght@400;600;700&display=swap">
<style>
:root{
  --brand:#8c0f22;
  --brand-dark:#6f0a19;
  --ink:#2b2b2b;
  --text:#444;
  --muted:#5a5a5a;
  --panel:#ffffff;
  --soft:#f2eff0;
  --news-bg:#ededee;
  --footer:#2e2e2e;
  --social:#2f4fb0;
  --social-2:#16245e;
}
*{box-sizing:border-box;margin:0;padding:0}
html,body{width:1200px;height:3712px;overflow:hidden;background:#fff}
body{font-family:"Overpass",Arial,sans-serif;color:var(--text);position:relative}
.page{position:relative;width:1200px;height:3712px;overflow:hidden}
.abs{position:absolute}
.layer{position:absolute;left:0;top:0;width:1200px;height:3712px}
.heading{font-family:"Poppins",Arial,sans-serif;font-weight:700;color:var(--ink)}
.btn{position:absolute;background:var(--brand);color:#fff;font-family:"Poppins",Arial,sans-serif;font-weight:600;display:flex;align-items:center;justify-content:center;text-decoration:none}

/* header */
.brand-name{position:absolute;left:134px;top:38px;display:flex;align-items:center;gap:14px;font-family:"Poppins",Arial,sans-serif;font-weight:700;font-size:34px;letter-spacing:1px;color:var(--ink)}
.brand-name .mark{width:34px;height:34px;background:var(--brand)}
.follow{position:absolute;left:679px;top:35px;font-size:14px;color:var(--ink);display:flex;align-items:center;gap:8px}
.dot{width:27px;height:27px;border-radius:50%;display:inline-block}
.dot.a{background:var(--social)}
.dot.b{background:var(--social-2)}
.call{position:absolute;left:858px;top:22px;display:flex;align-items:center;gap:10px}
.call-ico{width:40px;height:40px;border-radius:50%;border:2px solid var(--brand);display:flex;align-items:center;justify-content:center}
.call small{display:block;font-size:14px;color:var(--ink)}
.call strong{display:block;font-size:25px;font-weight:400;color:var(--brand);line-height:1.1}
.nav{position:absolute;top:84px;left:496px;display:flex;gap:28px;font-size:16px;color:var(--ink)}
.nav a{color:var(--ink);text-decoration:none}
.nav a.active{color:var(--brand);font-weight:700;text-decoration:underline;text-underline-offset:4px}

/* hero */
.hero-title{position:absolute;left:757px;top:262px;font-family:"Poppins",Arial,sans-serif;font-weight:800;font-size:48px;line-height:58px;color:#fff;text-transform:uppercase}
.arrow{position:absolute;top:339px;width:35px;height:36px;background:#fff;display:flex;align-items:center;justify-content:center}
.badge{position:absolute;left:541px;top:634px;width:86px;height:86px;border-radius:50%;background:#fff;box-shadow:0 2px 10px rgba(0,0,0,.2);display:flex;align-items:center;justify-content:center}
.badge span{width:30px;height:30px;background:var(--brand)}

.intro-box{position:absolute;left:131px;top:752px;width:504px;height:353px;border:4px solid #fff;padding:30px 36px}
.intro-box h2{font-size:26px;line-height:36px;color:#2e2e2e}
.intro-box p{margin-top:18px;font-size:17px;line-height:25.5px;color:#333}

/* sections */
.section-title{position:absolute;left:0;width:1200px;text-align:center;font-size:32px}
.rule{position:absolute;height:3px;width:35px;background:var(--brand)}

.card{position:absolute;width:457px;height:249px;background:var(--panel);box-shadow:0 2px 12px rgba(0,0,0,.06)}
.card .icon{position:absolute;left:36px;top:38px;width:68px;height:68px}
.card h3{position:absolute;left:143px;top:42px;font-size:19px;color:var(--ink)}
.card p{position:absolute;left:143px;top:78px;width:270px;font-size:15px;line-height:21px;color:var(--muted)}
.card .btn{left:144px;top:180px;width:97px;height:32px;font-size:13px}

.strategy-photo{position:absolute;left:131px;top:2058px;width:501px;height:481px;background:linear-gradient(135deg,#eef0f1,#d9dde0 55%,#c9ced2)}
.strategy h2{position:absolute;left:687px;top:2098px;font-family:"Poppins",Arial,sans-serif;font-weight:700;font-size:32px;line-height:44px;color:var(--ink)}
.strategy h2 em{font-style:normal;color:var(--brand)}
.strategy p{position:absolute;left:689px;top:2240px;width:376px;font-size:15px;line-height:21px;color:var(--muted)}

.news{position:absolute;top:2755px;width:296px;height:444px;background:#fff;box-shadow:0 2px 12px rgba(0,0,0,.06)}
.news h3{position:absolute;left:28px;top:20px;font-size:17px;line-height:22px;color:var(--ink)}
.news .photo{position:absolute;left:0;top:74px;width:296px;height:211px}
.news p{position:absolute;left:28px;top:303px;width:245px;font-size:15px;line-height:21px;color:var(--muted)}
.news .btn{left:28px;top:382px;width:100px;height:33px;font-size:13px}

/* footer */
.f-item{position:absolute;top:3400px;display:flex;gap:18px;color:#eee;font-size:15px;line-height:21px}
.f-ico{width:40px;height:40px;border-radius:50%;background:var(--brand);display:flex;align-items:center;justify-content:center;flex:none}
.f-rule{position:absolute;background:#555}
.f-brand{position:absolute;left:131px;top:3510px;display:flex;align-items:center;gap:14px;font-family:"Poppins",Arial,sans-serif;font-weight:700;font-size:34px;letter-spacing:1px;color:#fff}
.f-brand .mark{width:34px;height:34px;background:#fff}
.f-menu{position:absolute;left:547px;top:3514px;color:#fff}
.f-menu b{display:block;font-size:14px;font-weight:700;letter-spacing:.5px}
.f-menu div{margin-top:14px;font-size:15px;color:#eee;word-spacing:2px}
.f-menu span{margin:0 12px;color:#ccc}
.f-follow{position:absolute;left:131px;top:3638px;display:flex;align-items:center;gap:12px;color:#fff;font-weight:700;font-size:14px}
.copy{position:absolute;right:134px;top:3644px;font-size:13px;color:#ddd}
</style>
</head>
<body>
<div class="page">

  <!-- background shapes -->
  <svg class="layer" viewBox="0 0 1200 3712" aria-hidden="true">
    <polygon points="0,1100 1200,1100 1200,1916 600,2003 0,1916" fill="#f2eff0"/>
    <rect x="0" y="2601" width="1200" height="780" fill="#ededee"/>
    <polygon points="0,3358 600,3264 1200,3358 1200,3712 0,3712" fill="#8c0f22"/>
    <polygon points="0,3372 600,3278 1200,3372 1200,3712 0,3712" fill="#2e2e2e"/>
  </svg>

  <svg class="layer" viewBox="0 0 1200 3712" role="img" aria-label="Photo: consultants reviewing a binder in a bright data-centre corridor">
    <defs>
      <linearGradient id="corridor" x1="0" y1="0" x2="1" y2="1">
        <stop offset="0" stop-color="#5f7fa8"/>
        <stop offset=".45" stop-color="#c8d5e4"/>
        <stop offset="1" stop-color="#7f95b3"/>
      </linearGradient>
    </defs>
    <polygon points="0,590 600,676 1200,590 1200,1160 600,1225 0,1160" fill="url(#corridor)"/>
  </svg>

  <svg class="layer" viewBox="0 0 1200 3712" role="img" aria-label="Photo: technician working at a server rack in a dark blue server room">
    <defs>
      <linearGradient id="servers" x1="0" y1="0" x2="1" y2="0">
        <stop offset="0" stop-color="#1d2fa0"/>
        <stop offset=".45" stop-color="#2a2f55"/>
        <stop offset="1" stop-color="#1c2b6e"/>
      </linearGradient>
    </defs>
    <polygon points="0,121 1200,121 1200,580 600,666 0,580" fill="url(#servers)"/>
    <polygon points="0,580 600,666 1200,580 1200,592 600,678 0,592" fill="#8c0f22"/>
  </svg>

  <!-- header -->
  <div class="brand-name"><span>BORK VENTURES</span><span class="mark"></span></div>
  <div class="follow">FOLLOW US <span class="dot a"></span><span class="dot b"></span></div>
  <div class="call">
    <div class="call-ico">
      <svg width="20" height="20" viewBox="0 0 24 24"><path d="M6.6 10.8a15 15 0 0 0 6.6 6.6l2.2-2.2c.3-.3.7-.4 1-.2 1.1.4 2.3.6 3.6.6.6 0 1 .4 1 1V20c0 .6-.4 1-1 1A17 17 0 0 1 3 4c0-.6.4-1 1-1h3.5c.6 0 1 .4 1 1 0 1.3.2 2.5.6 3.6.1.3 0 .7-.2 1z" fill="#8c0f22"/></svg>
    </div>
    <div><small>CALL US NOW</small><strong>555-010-4471</strong></div>
  </div>
  <nav class="nav">
    <a class="active" href="#">HOME</a><a href="#">ABOUT US</a><a href="#">SERVICES</a><a href="#">STRATEGY</a><a href="#">IT NEWS</a><a href="#">CONTACT US</a>
  </nav>

  <!-- hero -->
  <h1 class="hero-title">Network<br>Assessment</h1>
  <a class="btn" href="#" style="left:758px;top:393px;width:166px;height:61px;font-size:18px;font-weight:700">READ MORE</a>
  <div class="arrow" style="left:0"><svg width="12" height="16" viewBox="0 0 12 16"><path d="M9 2 3 8l6 6" stroke="#333" stroke-width="2" fill="none"/></svg></div>
  <div class="arrow" style="left:1166px"><svg width="12" height="16" viewBox="0 0 12 16"><path d="m3 2 6 6-6 6" stroke="#333" stroke-width="2" fill="none"/></svg></div>
  <div class="badge"><span></span></div>

  <div class="intro-box">
    <h2 class="heading">Bringing Thought Leadership and Quality to Every Project</h2>
    <p>Bork Ventures, Inc. is an 8(a) full-service IT consulting company based in the Washington, DC Metro area. We offer specialized, highly customized technology solutions for our customers located throughout the United States. Learn about our Services now.</p>
  </div>
  <a class="btn" href="#" style="left:179px;top:1026px;width:128px;height:43px;font-size:16px">Read More</a>

  <!-- services -->
  <h2 class="section-title heading" style="top:1262px">Our Services</h2>
  <div class="rule" style="left:583px;top:1318px"></div>

  <div class="card" style="left:131px;top:1369px">
    <svg class="icon" viewBox="0 0 68 68" fill="none" stroke="#8c0f22" stroke-width="2.2"><rect x="12" y="12" width="44" height="44"/><rect x="20" y="20" width="28" height="28"/><rect x="27" y="27" width="14" height="14"/><path d="M20 4v8M28 4v8M36 4v8M44 4v8M20 56v8M28 56v8M36 56v8M44 56v8M4 20h8M4 28h8M4 36h8M4 44h8M56 20h8M56 28h8M56 36h8M56 44h8"/></svg>
    <h3 class="heading">Hardware / Software Sales</h3>
    <p>We have access to multiple distributor partners throughout North America, as well as Elite Partner Status with many of the industry’s</p>
    <a class="btn" href="#">Read More</a>
  </div>
  <div class="card" style="left:611px;top:1369px">
    <svg class="icon" viewBox="0 0 68 68" fill="none" stroke="#8c0f22" stroke-width="2.2"><circle cx="34" cy="18" r="12"/><path d="M10 64V50c0-8 8-12 24-12s24 4 24 12v14H10zM34 38l-4 8 4 18 4-18z"/><text x="44" y="56" font-size="12" fill="#8c0f22" stroke="none" font-family="Arial">$</text></svg>
    <h3 class="heading">Professional Services</h3>
    <p>Our team provides experienced leadership and guidance, utilizing the industry standard methodologies.</p>
    <a class="btn" href="#">Read More</a>
  </div>
  <div class="card" style="left:131px;top:1643px">
    <svg class="icon" viewBox="0 0 68 68" fill="none" stroke="#8c0f22" stroke-width="2.2"><rect x="8" y="4" width="48" height="38" rx="2"/><rect x="14" y="10" width="36" height="26"/><path d="M26 42v8h12v-8M20 54h24"/><rect x="44" y="48" width="12" height="18" rx="6"/><path d="M50 48v6"/></svg>
    <h3 class="heading">Technology Assessment</h3>
    <p>Experience has shown companies that perform objective, third-party technology assessments have proven to be instrumental in identifying</p>
    <a class="btn" href="#">Read More</a>
  </div>
  <div class="card" style="left:611px;top:1643px">
    <svg class="icon" viewBox="0 0 68 68" fill="none" stroke="#8c0f22" stroke-width="2.6"><path d="M6 6h56v40H22L8 60V6"/><path d="M16 18h36M16 26h36M16 34h24"/></svg>
    <h3 class="heading">Technology Consulting</h3>
    <p>Implementing quality solutions is more than applying technology to problems. You need experts with deep technical knowledge</p>
    <a class="btn" href="#">Read More</a>
  </div>

  <!-- strategy -->
  <div class="strategy-photo" role="img" aria-label="Photo: overhead view of a team meeting around a round white table with laptops"></div>
  <section class="strategy">
    <h2><em>Our Strategy</em><br>Your Path to Success</h2>
    <div class="rule" style="left:688px;top:2196px"></div>
    <p>Civilian and Federal agencies are facing increased demands driven by the changing economic environment and shifts in the way products and services are sold and delivered. These factors have created an imperative to leverage new and innovative technology solution architectures like cloud computing to help reduce cost and deliver profit-driving IT capabilities faster than ever before</p>
    <a class="btn" href="#" style="left:693px;top:2447px;width:128px;height:43px;font-size:16px">Read More</a>
  </section>

  <!-- news -->
  <h2 class="section-title heading" style="top:2654px">IT News</h2>
  <div class="rule" style="left:578px;top:2703px"></div>

  <article class="news" style="left:125px">
    <h3 class="heading">Lorem Ipsum is simply<br>dummy text of the.</h3>
    <div class="photo" role="img" aria-label="Photo: team in an office watching a presenter at a whiteboard" style="background:linear-gradient(135deg,#9aa3ab,#d9dde0 60%,#b4bac0)"></div>
    <p>Lorem ipsum dolor sit amet, cons ectetur adipiscing elit, sed do eiusmod tempor incidid.</p>
    <a class="btn" href="#">Read More</a>
  </article>
  <article class="news" style="left:447px">
    <h3 class="heading">Lorem Ipsum is simply<br>dummy text of the.</h3>
    <div class="photo" role="img" aria-label="Photo: two hands joining red puzzle pieces on a blue-grey background" style="background:linear-gradient(135deg,#7f93ab,#a8b7c8 55%,#8a9db3)"></div>
    <p>Lorem ipsum dolor sit amet, cons ectetur adipiscing elit, sed do eiusmod tempor incidid.</p>
    <a class="btn" href="#">Read More</a>
  </article>
  <article class="news" style="left:768px">
    <h3 class="heading">Lorem Ipsum is simply<br>dummy text of the.</h3>
    <div class="photo" role="img" aria-label="Photo: person taking notes beside a tablet showing charts" style="background:linear-gradient(135deg,#5c5f63,#b9bcbf 55%,#8e9195)"></div>
    <p>Lorem ipsum dolor sit amet, cons ectetur adipiscing elit, sed do eiusmod tempor incidid.</p>
    <a class="btn" href="#">Read More</a>
  </article>

  <div class="badge" style="top:3243px;left:543px;width:68px;height:68px"><span style="width:24px;height:24px"></span></div>

  <!-- footer -->
  <div class="f-item" style="left:131px">
    <span class="f-ico"><svg width="12" height="16" viewBox="0 0 12 16"><path d="M6 0a6 6 0 0 0-6 6c0 4.5 6 10 6 10s6-5.5 6-10a6 6 0 0 0-6-6zm0 8.2A2.2 2.2 0 1 1 6 3.8a2.2 2.2 0 0 1 0 4.4z" fill="#fff"/></svg></span>
    <div>2280 Quarry Hollow Rd<br>Fenwick, MD 20990</div>
  </div>
  <div class="f-item" style="left:511px">
    <span class="f-ico"><svg width="14" height="14" viewBox="0 0 24 24"><path d="M6.6 10.8a15 15 0 0 0 6.6 6.6l2.2-2.2c.3-.3.7-.4 1-.2 1.1.4 2.3.6 3.6.6.6 0 1 .4 1 1V20c0 .6-.4 1-1 1A17 17 0 0 1 3 4c0-.6.4-1 1-1h3.5c.6 0 1 .4 1 1 0 1.3.2 2.5.6 3.6.1.3 0 .7-.2 1z" fill="#fff"/></svg></span>
    <div>Call Us now on<br>555-010-4471</div>
  </div>
  <div class="f-item" style="left:820px">
    <span class="f-ico"><svg width="14" height="11" viewBox="0 0 14 11"><path d="M0 0h14v11H0z" fill="#fff"/><path d="M0 0l7 6 7-6" stroke="#8c0f22" stroke-width="1.4" fill="none"/></svg></span>
    <div>E mail us<br>info@borkventuresinc.example</div>
  </div>

  <div class="f-rule" style="left:131px;top:3473px;width:937px;height:1px"></div>
  <div class="f-rule" style="left:474px;top:3473px;width:1px;height:119px"></div>

  <div class="f-brand"><span>BORK VENTURES</span><span class="mark"></span></div>
  <div class="f-menu">
    <b>MENU</b>
    <div>Home<span>/</span>About us<span>/</span>Services<span>/</span>Strategy<span>/</span>IT News<span>/</span>Contact us</div>
  </div>

  <div class="f-follow">FOLLOW US <span class="dot a"></span><span class="dot b"></span></div>
  <div class="copy">Copyright 2019 All Rights Reserved</div>
</div>
</body>
</html>
```